New Business Card for Software Company

We are looking at rebranding a 10 year old company that specializes in PDF and DWF solutions for Architects and Engineers. We will attach the new company logo that we are going with so you can work with that and complimentary colors.
The sample information we would like on the business card is:
Gerald Pinfold
Vice President
4738 W. Harrowgate Lane. STE 305
PMB#417
Corvale, NV 85374
866-392-5074 US Toll Free
123-456-3190 Cell
gpinfold@plavorix.com
The old tag line that we had on the business cars was.
Delivering Dependable PDF and DWF Tools for Design Professionals Everywhere.
If you have an idea for a better tag line we are open to that also.
Updates
We would like to thank all of the Designers for their wonderful work. We apologize that we will not have the time to provide feedback to everyone. There is just so many innovative and professional designs that you have all created making our decision even harder.
Target Market(s)
Architects and Engineers
Industry/Entity Type
Business
Look and feel

```html
<!DOCTYPE html>
<html lang="en">
<head>
<meta charset="utf-8">
<title>Plavorix Business Card</title>
<link rel="stylesheet" href="https://fonts.googleapis.com/css2?family=Open+Sans:wght@400;600;700;800&display=swap">
<style>
  :root {
    --stage: #e9e6e2;
    --card: #ffffff;
    --orange: #f26a1b;
    --orange-light: #f7931e;
    --red: #c1272d;
    --grey: #6d6e71;
    --grey-dark: #58595b;
    --ink-light: #ffffff;
  }
  * { margin: 0; padding: 0; box-sizing: border-box; }
  html, body { width: 1200px; height: 720px; overflow: hidden; }
  body {
    background: var(--stage);
    font-family: "Open Sans", Arial, sans-serif;
    position: relative;
  }
  .card {
    position: absolute;
    width: 540px;
    height: 310px;
    background: var(--card);
    box-shadow: 0 8px 22px rgba(0,0,0,.18);
    overflow: hidden;
  }
  .card--front { left: 50px; top: 120px; }
  .card--back { left: 610px; top: 290px; }

  .card__accent {
    position: absolute; top: 0; right: 0; bottom: 0; width: 218px;
    background: linear-gradient(160deg, var(--orange-light) 0%, var(--orange) 45%, var(--red) 100%);
  }

  .brand { position: absolute; display: flex; align-items: center; }
  .brand__dot { border-radius: 50%; background: var(--orange); flex: none; }
  .brand__name { font-weight: 800; color: var(--orange); letter-spacing: -1px; line-height: 1; }

  .card--front .brand { left: 36px; top: 62px; }
  .card--front .brand__dot { width: 40px; height: 40px; margin-right: 12px; }
  .card--front .brand__name { font-size: 44px; }

  .holder { position: absolute; left: 42px; top: 200px; }
  .holder__name { font-size: 15px; font-weight: 700; color: var(--orange); }
  .holder__title { font-size: 11px; color: var(--grey); margin-top: 1px; }

  .contact {
    position: absolute; left: 340px; top: 112px; width: 186px;
    list-style: none; color: var(--ink-light); font-size: 10.5px; line-height: 1.5;
  }
  .contact__item { display: flex; align-items: center; gap: 7px; margin-bottom: 4px; }
  .contact__icon { width: 11px; height: 11px; flex: none; }
  .contact__address { margin-top: 8px; }

  .card--back .brand { left: 118px; top: 92px; }
  .card--back .brand__dot { width: 56px; height: 56px; margin-right: 14px; }
  .card--back .brand__name { font-size: 64px; }

  .tagline {
    position: absolute; left: 0; right: 0; top: 205px;
    text-align: center; text-transform: uppercase;
    font-size: 14px; font-weight: 600; color: var(--grey-dark); line-height: 1.4;
  }
</style>
</head>
<body>

<section class="card card--front" aria-label="Business card front">
  <div class="card__accent" role="img" aria-label="Orange to red colour panel behind contact details"></div>

  <div class="brand">
    <span class="brand__dot"></span>
    <span class="brand__name">Plavorix</span>
  </div>

  <div class="holder">
    <p class="holder__name">Gerald Pinfold</p>
    <p class="holder__title">Vice President</p>
  </div>

  <ul class="contact">
    <li class="contact__item">
      <svg class="contact__icon" viewBox="0 0 12 12" aria-hidden="true"><path d="M2.5,1 L4.5,1 L5.3,3.6 L4,4.6 C4.7,6 5.9,7.3 7.4,8 L8.4,6.7 L11,7.5 L11,9.5 C6.5,10.2 1.8,5.5 2.5,1Z" fill="#fff"/></svg>
      <span>866-392-5074 US(TF)</span>
    </li>
    <li class="contact__item">
      <svg class="contact__icon" viewBox="0 0 12 12" aria-hidden="true"><rect x="3" y="0.8" width="6" height="10.4" rx="1" fill="none" stroke="#fff" stroke-width="1.2"/><rect x="4.2" y="2.2" width="3.6" height="5" fill="#fff"/><circle cx="6" cy="9.2" r=".7" fill="#fff"/></svg>
      <span>123-456-3190</span>
    </li>
    <li class="contact__item">
      <svg class="contact__icon" viewBox="0 0 12 12" aria-hidden="true"><rect x="1" y="2.5" width="10" height="7" rx="1" fill="#fff"/><path d="M1.5,3 L6,6.6 L10.5,3" fill="none" stroke="#c1272d" stroke-width="1"/></svg>
      <span>gpinfold@plavorix.com</span>
    </li>
    <li class="contact__address">
      4738 W. Harrowgate Lane. STE 305<br>
      PMB#417, Corvale, NV 85374
    </li>
  </ul>
</section>

<section class="card card--back" aria-label="Business card back">
  <div class="brand">
    <span class="brand__dot"></span>
    <span class="brand__name">Plavorix</span>
  </div>
  <p class="tagline">
    Delivering dependable PDF and DWF tools<br>
    for design professionals everywhere
  </p>
</section>

</body>
</html>
```